Brightfen Business Card Redesign & Logo Update

We need to update our business cards to something more modern and fresh. Brightfen can provide the current color schemes and old design examples, but welcome creativity in helping us with this redesign. PLEASE NOTE that we no longer utilize the "tree" and/or "leaf" imagery in our branding. If able would apprecaite an update on the quality of our "words only" logo in Ai. / PNG formats too.

Target Market(s)

Investors, landowners, corporate partners, contractors

Industry/Entity Type

Environmental Restoration & Conservation

Contact Information for Business Card

Logo, persons name, title, mailing address, phone and email, website url

Font styles to use
Other font styles liked:
• Merriweather

Requirements
Nice to have
• Logo, persons name, title, mailing address, phone and email, website url, but open to ideams
Should not have
• No all back backgrounds

```html
<!DOCTYPE html>
<html lang="en">
<head>
<meta charset="utf-8">
<title>Brightfen Business Card</title>
<link rel="stylesheet" href="https://fonts.googleapis.com/css2?family=Oswald:wght@600&family=Montserrat:wght@400;700&display=swap">
<style>
  :root {
    --backdrop: #d4d5d7;
    --charcoal: #35352f;
    --orange: #ef8627;
    --green: #1b8540;
    --ink: #1c1c1c;
    --paper: #ffffff;
  }
  * { margin: 0; padding: 0; box-sizing: border-box; }
  html, body {
    width: 900px; height: 1200px; overflow: hidden;
    background: var(--backdrop);
    font-family: "Montserrat", sans-serif;
  }
  .canvas { position: relative; width: 900px; height: 1200px; }
  .card {
    position: absolute; left: 121px; width: 657px; height: 375px;
    border-radius: 14px; overflow: hidden;
  }
  .card-front { top: 204px; background: var(--charcoal); }
  .card-back { top: 621px; background: var(--paper); }

  .wordmark {
    font-family: "Oswald", sans-serif; font-weight: 600;
    color: var(--orange); text-transform: uppercase; line-height: 1;
  }
  .tagline {
    font-family: "Oswald", sans-serif; font-weight: 600;
    text-transform: uppercase; line-height: 1; white-space: nowrap;
  }
  .card-front .brand {
    position: absolute; top: 122px; left: 0; width: 100%; text-align: center;
  }
  .card-front .wordmark { font-size: 98px; letter-spacing: 1px; }
  .card-front .tagline { font-size: 30px; color: var(--paper); margin-top: 6px; letter-spacing: 0.2px; }

  .social { position: absolute; top: 315px; left: 0; width: 100%; text-align: center; font-size: 0; }
  .social-dot {
    display: inline-block; width: 32px; height: 32px; border-radius: 50%;
    margin: 0 6px; background: var(--green);
  }
  .social-dot.alt { background: var(--orange); }

  .card-back .brand { position: absolute; top: 30px; left: 40px; }
  .card-back .wordmark { font-size: 70px; letter-spacing: 0.5px; }
  .card-back .tagline { font-size: 21px; color: var(--ink); margin-top: 3px; margin-left: 8px; }

  .person { position: absolute; top: 38px; right: 40px; text-align: right; }
  .person-name { font-weight: 700; font-size: 24px; letter-spacing: 1px; text-transform: uppercase; }
  .person-name .first { color: var(--orange); }
  .person-name .last { color: var(--green); }
  .person-title { font-size: 15px; color: var(--ink); margin-top: 2px; }

  .contact { position: absolute; top: 268px; left: 38px; list-style: none; }
  .contact li {
    display: flex; align-items: center; height: 24px;
    font-size: 16px; letter-spacing: 0.6px; color: var(--ink);
  }
  .contact svg { width: 14px; height: 14px; margin-right: 7px; fill: var(--orange); }

  .address {
    position: absolute; top: 292px; right: 40px; text-align: right;
    font-size: 15.5px; line-height: 24px; color: var(--ink); font-style: normal;
  }

  .band { position: absolute; bottom: 0; height: 11px; }
  .band-orange { left: 0; width: 326px; background: var(--orange); }
  .band-green { left: 330px; right: 0; background: var(--green); }
</style>
</head>
<body>
<main class="canvas">
  <section class="card card-front">
    <div class="brand">
      <div class="wordmark">Brightfen</div>
      <div class="tagline">Environmental Credit Company</div>
    </div>
    <div class="social" aria-label="Social profiles">
      <span class="social-dot"></span><span class="social-dot alt"></span><span class="social-dot"></span>
    </div>
  </section>

  <section class="card card-back">
    <div class="brand">
      <div class="wordmark">Brightfen</div>
      <div class="tagline">Environmental Credit Company</div>
    </div>
    <div class="person">
      <div class="person-name"><span class="first">Dana</span> <span class="last">Keller</span></div>
      <div class="person-title">Director</div>
    </div>
    <ul class="contact">
      <li><svg viewBox="0 0 24 24" aria-hidden="true"><path d="M6.6 10.8a15.2 15.2 0 0 0 6.6 6.6l2.2-2.2a1 1 0 0 1 1-.25 11.4 11.4 0 0 0 3.6.57 1 1 0 0 1 1 1V20a1 1 0 0 1-1 1A17 17 0 0 1 3 4a1 1 0 0 1 1-1h3.5a1 1 0 0 1 1 1c0 1.25.2 2.45.57 3.6a1 1 0 0 1-.25 1z"/></svg>(555) 014-2280</li>
      <li><svg viewBox="0 0 24 24" aria-hidden="true"><path d="M2 5h20v2l-10 6L2 7z"/><path d="M2 9l10 6 10-6v10H2z"/></svg>info@brightfencredits.com</li>
      <li><svg viewBox="0 0 24 24" aria-hidden="true"><path d="M12 2a10 10 0 1 0 0 20 10 10 0 0 0 0-20zm0 2c.9 0 2.2 1.9 2.8 5H9.2C9.8 5.9 11.1 4 12 4zM4.3 11h4.5a17 17 0 0 0 .1 2H4.3a8 8 0 0 1 0-2zm10.9 0h4.5a8 8 0 0 1 0 2h-4.6a17 17 0 0 0 .1-2zM9.2 15h5.6c-.6 3.1-1.9 5-2.8 5s-2.2-1.9-2.8-5z"/></svg>www.brightfencredits.com</li>
    </ul>
    <address class="address">4820 Meadow Road 17,<br>Alder, TX 75000</address>
    <div class="band band-orange"></div>
    <div class="band band-green"></div>
  </section>
</main>
</body>
</html>
```